Website for new slot-booking/reservations website/software

For a new software product we need a brand new logo and website for a reservations/booking system. The website should ideally present the main features with information text, contact info, news page as well as registration and pricing pages. As currently primary field of operation the software should be used for tennis but later on, also for other sport types. Also we'd like to be the logo a text-brand which includes the name "zeitfeldo.com" or just "zeitfeldo". The logo should ideally include an icon-design in some way. Generally we are open for ideas.

Bootstrap 4 template is a minimum requirement. (Multi-Page preferred, Single-Page still OK.)

You can use the attached image as an inspiration, but change of colors or other design elements are up to you. Currently the application has a primary color of #5500ff. The website created by you will not include the application itself, so it can have different (but ideally similar) Look&Feel.
Updates

Target Market(s)

Sports, Club-Management

Logo Text

zeitfeldo.com

Coding

Coded - Design and coding required

Number of Pages Required

5+ page

Font styles to use
Sans Serif

Requirements
Must have
• Bootstrap 4 Template, SCSS
Nice to have
• Rapid Loading Times, not too much external JS Libraries.
Should not have
• Extensive animations

```html
<!DOCTYPE html>
<html lang="en">
<head>
<meta charset="utf-8">
<title>Zeitfeldo – Reservation Tennis Software</title>
<link rel="stylesheet" href="https://fonts.googleapis.com/css2?family=Montserrat:wght@500;600;700;800&family=Open+Sans:wght@400;600&display=swap">
<style>
:root{
  --brand:#5500ff;
  --ink:#3b3b3b;
  --text:#555555;
  --muted:#9a9a9a;
  --soft:#f4f1f1;
  --soft-blue:#eef0f8;
  --white:#ffffff;
  --footer:#1f1f1f;
  --footer-text:#cfcfcf;
}
*{box-sizing:border-box;margin:0;padding:0}
html,body{width:1200px;height:4376px;overflow:hidden}
body{position:relative;background:var(--white);font-family:"Open Sans",Arial,sans-serif;color:var(--text)}
.abs{position:absolute}
.heading{font-family:"Montserrat",Arial,sans-serif;font-weight:800;color:var(--ink)}
.btn{position:absolute;display:flex;align-items:center;justify-content:center;background:var(--brand);color:var(--white);font-family:"Montserrat",Arial,sans-serif;font-weight:700;letter-spacing:.3px;text-transform:uppercase}
.btn-offset::after{content:"";position:absolute;left:4px;top:4px;right:-4px;bottom:-4px;border:2px solid var(--brand);pointer-events:none}
.section-title{position:absolute;left:0;width:1200px;text-align:center;font-size:24px;letter-spacing:.5px}
.title-rule{position:absolute;left:581px;width:38px;height:3px;background:#a9a9a9}

/* header / hero */
.hero{left:0;top:0;width:1200px;height:609px;background:linear-gradient(180deg,#5f7fd6 0%,#8ea6e4 45%,#b4c3ee 100%)}
.hero-photo{left:0;top:0;width:600px;height:609px;background:radial-gradient(ellipse at 45% 55%,rgba(240,235,235,.55) 0%,rgba(200,190,200,.25) 35%,rgba(0,0,0,0) 65%)}
.logo{display:flex;align-items:center;gap:10px;font-family:"Montserrat",Arial,sans-serif;font-weight:800;color:var(--white);text-transform:uppercase;line-height:1}
.logo-mark{width:22px;height:22px;border:3px solid currentColor;border-radius:50%;flex:none}
.nav{position:absolute;left:425px;top:32px;width:540px;height:20px;font-family:"Montserrat",Arial,sans-serif;font-weight:700;font-size:14px;line-height:20px;color:var(--white)}
.nav a{position:absolute;top:0;white-space:nowrap;text-decoration:none;color:inherit}
.nav-register{position:absolute;left:974px;top:24px;width:92px;height:34px;border:2px solid var(--white);color:var(--white);font-family:"Montserrat",Arial,sans-serif;font-weight:700;font-size:13px;display:flex;align-items:center;justify-content:center}
.hero-title{left:665px;top:199px;font-size:36px;line-height:49px;color:#2f3340}
.hero-lead{left:667px;top:313px;width:410px;font-family:"Montserrat",Arial,sans-serif;font-size:18px;line-height:28px;color:#3a3f4d}
.dots{left:563px;top:560px;display:flex;gap:11px}
.dots i{width:7px;height:7px;border-radius:50%;background:rgba(255,255,255,.75)}
.dots i.on{background:var(--brand)}

/* features */
.feature-icon{width:74px;height:74px;border:3px solid var(--brand);border-radius:50%;display:flex;align-items:center;justify-content:center}
.feature-title{font-family:"Montserrat",Arial,sans-serif;font-weight:700;font-size:14px;color:#333}
.feature-text{font-size:13px;line-height:19px;color:#444;width:290px;margin-top:9px}
.divider{left:593px;top:743px;width:1px;height:362px;background:#dcdcdc}

/* welcome */
.welcome{left:0;top:1249px;width:1200px;height:451px;background:var(--soft)}
.welcome-photo{left:0;top:0;width:600px;height:451px;background:linear-gradient(90deg,#b9b5ae 0%,#cdc9c3 40%,#e6e2df 70%,rgba(244,241,241,0) 100%)}
.welcome-kicker{left:632px;top:50px;font-size:19px;font-weight:700}
.welcome-name{left:632px;top:76px;font-size:33px}
.welcome-text{left:632px;top:168px;width:436px;font-size:15.5px;line-height:25.6px;color:#444}

/* pricing */
.plan{position:absolute;background:var(--white);box-shadow:0 0 18px rgba(0,0,0,.08);text-align:center}
.plan-price{font-family:"Montserrat",Arial,sans-serif;font-weight:800;font-size:26px;color:var(--brand)}
.plan-name{font-family:"Montserrat",Arial,sans-serif;font-weight:800;font-size:24px;color:#333;margin-top:8px;letter-spacing:.5px}
.plan-row{margin:0 auto;width:238px;font-size:12.5px;line-height:17px;color:#444;padding:13px 14px 12px;border-bottom:1px solid #e3e3e3}
.plan-row:last-of-type{border-bottom:0}
.plan-featured{background:var(--brand);box-shadow:none}
.plan-featured .plan-price,.plan-featured .plan-name{color:var(--white)}
.plan-featured .plan-row{color:#e4dcff;border-color:rgba(255,255,255,.45)}

/* news */
.news{left:0;top:2394px;width:1200px;height:557px;background:var(--soft)}
.news-card{position:absolute;top:135px;width:296px;height:364px;background:var(--white)}
.news-photo{width:296px;height:176px}
.news-title{position:absolute;left:24px;top:196px;width:250px;font-family:"Montserrat",Arial,sans-serif;font-weight:700;font-size:14.5px;line-height:19px;color:#333}
.news-text{position:absolute;left:24px;top:248px;width:240px;font-size:11.5px;line-height:15px;color:#555}

/* benefits */
.benefit-photo{left:570px;top:2953px;width:630px;height:602px;background:linear-gradient(160deg,#4f5f4a 0%,#6d6c52 35%,#9a6a45 70%,#c07a4a 100%)}
.benefit{position:absolute;left:131px;width:481px;height:157px;background:var(--white);border-left:13px solid var(--brand)}
.benefit-icon{position:absolute;left:57px;top:28px}
.benefit-title{position:absolute;left:136px;top:33px;font-family:"Montserrat",Arial,sans-serif;font-weight:800;font-size:18px;color:#333}
.benefit-text{position:absolute;left:136px;top:64px;width:310px;font-size:12px;line-height:17.5px;color:#444}

/* cta */
.cta{left:0;top:3618px;width:1200px;height:418px;background:var(--soft-blue)}
.cta-photo{left:0;top:0;width:640px;height:418px;background:linear-gradient(90deg,#43506e 0%,#6c7896 35%,#b8bfd2 70%,rgba(238,240,248,0) 100%)}
.cta-title{left:651px;top:96px;width:400px;font-family:"Montserrat",Arial,sans-serif;font-weight:600;font-size:25px;line-height:31px;color:#333}
.cta-text{left:651px;top:175px;width:430px;font-size:13.5px;line-height:21.5px;color:#444}

/* footer */
.footer{left:0;top:4036px;width:1200px;height:340px;background:var(--footer);color:var(--footer-text)}
.footer-head{position:absolute;top:49px;font-family:"Montserrat",Arial,sans-serif;font-weight:700;font-size:13px;color:var(--white);letter-spacing:.5px}
.footer-menu{position:absolute;left:498px;top:86px;list-style:none;font-size:12px;line-height:20px;text-transform:uppercase}
.footer-item{position:absolute;display:flex;align-items:center;gap:10px;font-size:11.5px;line-height:15px}
.footer-dot{width:22px;height:22px;border-radius:50%;background:var(--white);flex:none;display:flex;align-items:center;justify-content:center}
.footer-rule{position:absolute;left:131px;top:263px;width:938px;height:1px;background:#3a3a3a}
.copyright{position:absolute;left:0;width:1200px;top:304px;text-align:center;font-size:10px;color:#bdbdbd}
</style>
</head>
<body>

<!-- Header & hero -->
<header class="abs hero">
  <div class="abs hero-photo" role="img" aria-label="Photo of a tennis player serving against a bright blue sky"></div>
  <div class="abs logo" style="left:131px;top:29px;font-size:21px"><span class="logo-mark"></span>Zeitfeldo</div>
  <nav class="nav">
    <a style="left:0">HOME</a>
    <a style="left:85px">ABOUT US</a>
    <a style="left:207px">FEATURES</a>
    <a style="left:325px">PRICING</a>
    <a style="left:427px">CONTACT US</a>
  </nav>
  <div class="nav-register">REGISTER</div>
  <h1 class="abs heading hero-title">RESERVATION<br>TENNIS SOFTWARE</h1>
  <p class="abs hero-lead">Lorem Ipsum is simply dummy text of the printing and typesetting industry</p>
  <div class="btn" style="left:670px;top:400px;width:122px;height:40px;font-size:13px">Read More</div>
  <div class="abs dots"><i></i><i></i><i class="on"></i><i></i><i></i></div>
</header>

<!-- Features -->
<section>
  <h2 class="heading section-title" style="top:655px">FEATURES</h2>
  <div class="title-rule" style="top:698px"></div>
  <div class="abs divider"></div>

  <div class="abs feature-icon" style="left:131px;top:752px"><svg width="36" height="36" viewBox="0 0 36 36" fill="none" stroke="#5500ff" stroke-width="2"><rect x="4" y="5" width="26" height="20" rx="1"/><path d="M4 10h26M10 16h14M10 20h8"/><circle cx="27" cy="27" r="5"/><path d="M25 27l2 2 3-3"/></svg></div>
  <div class="abs" style="left:230px;top:742px"><div class="feature-title">Recurring Reservations</div><p class="feature-text">Lorem Ipsum is simply dummy text of the printing and typesetting industry more-or-less normal distribution of letters</p></div>

  <div class="abs feature-icon" style="left:131px;top:890px"><svg width="36" height="36" viewBox="0 0 36 36" fill="none" stroke="#5500ff" stroke-width="2"><path d="M8 4h16l5 5v23H8z"/><path d="M13 13h11M13 18h11M13 23h7"/><circle cx="26" cy="27" r="4"/></svg></div>
  <div class="abs" style="left:230px;top:881px"><div class="feature-title">Club Rules</div><p class="feature-text">Lorem Ipsum is simply dummy text of the printing and typesetting industry more-or-less normal distribution of letters</p></div>

  <div class="abs feature-icon" style="left:131px;top:1032px"><svg width="36" height="36" viewBox="0 0 36 36" fill="none" stroke="#5500ff" stroke-width="2"><path d="M18 4l12 5v9c0 7-6 12-12 14C12 30 6 25 6 18V9z"/><circle cx="18" cy="16" r="4"/><path d="M11 26c2-4 12-4 14 0"/></svg></div>
  <div class="abs" style="left:230px;top:1024px"><div class="feature-title">Member Security</div><p class="feature-text">Lorem Ipsum is simply dummy text of the printing and typesetting industry more-or-less normal distribution of letters</p></div>

  <div class="abs" style="left:668px;top:742px"><div class="feature-title">Member Payments</div><p class="feature-text">Lorem Ipsum is simply dummy text of the printing and typesetting industry more-or-less normal distribution of letters</p></div>
  <div class="abs feature-icon" style="left:991px;top:752px"><svg width="36" height="36" viewBox="0 0 36 36" fill="none" stroke="#5500ff" stroke-width="2"><ellipse cx="18" cy="9" rx="11" ry="4"/><path d="M7 9v6c0 2 5 4 11 4s11-2 11-4V9M7 15v6c0 2 5 4 11 4s11-2 11-4v-6M7 21v6c0 2 5 4 11 4s11-2 11-4v-6"/></svg></div>

  <div class="abs" style="left:668px;top:881px"><div class="feature-title">Club Reports</div><p class="feature-text">Lorem Ipsum is simply dummy text of the printing and typesetting industry more-or-less normal distribution of letters</p></div>
  <div class="abs feature-icon" style="left:991px;top:890px"><svg width="36" height="36" viewBox="0 0 36 36" fill="none" stroke="#5500ff" stroke-width="2"><rect x="4" y="6" width="28" height="19"/><path d="M18 25v6M12 31h12M9 21v-5M13 21v-8M17 21v-3"/><circle cx="25" cy="15" r="4"/></svg></div>

  <div class="abs" style="left:668px;top:1024px"><div class="feature-title">Member Registration</div><p class="feature-text">Lorem Ipsum is simply dummy text of the printing and typesetting industry more-or-less normal distribution of letters</p></div>
  <div class="abs feature-icon" style="left:991px;top:1032px"><svg width="36" height="36" viewBox="0 0 36 36" fill="none" stroke="#5500ff" stroke-width="2"><path d="M8 4h17v28H8z"/><path d="M12 11h9M12 16h9M12 21h5"/><path d="M30 14l-9 12-3 1 1-3 9-12z"/></svg></div>

  <div class="btn btn-offset" style="left:522px;top:1151px;width:156px;height:32px;font-size:11px">View All Features</div>
</section>

<!-- Welcome -->
<section class="abs welcome">
  <div class="abs welcome-photo" role="img" aria-label="Photo of a smiling man working on a laptop in a bright office"></div>
  <div class="abs heading welcome-kicker">Welcome to</div>
  <h2 class="abs heading welcome-name">Zeitfeldo</h2>
  <div class="abs" style="left:632px;top:126px;width:38px;height:3px;background:#a9a9a9"></div>
  <p class="abs welcome-text">There are many variations of passages of Lorem Ipsum available, but the majority have suffered alteration in some form, by injected humour, or randomised words which don't look even slightly believable. If you are going to use a passage of Lorem Ipsum, you need to be sure there isn't anything embarrassing hidden in the middle of text.</p>
  <div class="btn btn-offset" style="left:636px;top:357px;width:105px;height:33px;font-size:11px">Read More</div>
</section>

<!-- Pricing -->
<section>
  <h2 class="heading section-title" style="top:1750px">OUR PRICING</h2>
  <div class="title-rule" style="top:1797px"></div>

  <div class="plan" style="left:131px;top:1865px;width:301px;height:443px;padding-top:40px">
    <div class="plan-price">$0.00</div>
    <div class="plan-name">FREE</div>
    <div style="margin-top:18px">
      <p class="plan-row">There are many variations of pass ages of Lorem Ipsum available.</p>
      <p class="plan-row">Lorem ipsum dolor sit amet, consectetur adipiscing elit.</p>
      <p class="plan-row">Sed ut perspiciatis unde omnis iste natus error</p>
      <p class="plan-row">At vero eos et accusamus et iusto odio dignissimos ducimus.</p>
    </div>
    <div class="btn" style="left:106px;top:384px;width:90px;height:29px;font-size:11px">Register</div>
  </div>

  <div class="plan plan-featured" style="left:449px;top:1839px;width:301px;height:495px;padding-top:30px">
    <div class="plan-price" style="font-size:27px">$20.00</div>
    <div class="plan-name">ENTERPRISE</div>
    <div style="margin-top:16px">
      <p class="plan-row">There are many variations of pass ages of Lorem Ipsum available.</p>
      <p class="plan-row">Lorem ipsum dolor sit amet, consectetur adipiscing elit.</p>
      <p class="plan-row">Sed ut perspiciatis unde omnis iste natus error</p>
      <p class="plan-row">At vero eos et accusamus et iusto odio dignissimos ducimus.</p>
      <p class="plan-row">Lorem ipsum dolor sit amet, consectetur adipiscing elit.</p>
    </div>
    <div class="btn" style="left:106px;top:436px;width:90px;height:29px;font-size:11px;background:var(--white);color:var(--brand)">Register</div>
  </div>

  <div class="plan" style="left:770px;top:1865px;width:303px;height:443px;padding-top:40px">
    <div class="plan-price">$50.00</div>
    <div class="plan-name">BUSINESS</div>
    <div style="margin-top:18px">
      <p class="plan-row">There are many variations of pass ages of Lorem Ipsum available.</p>
      <p class="plan-row">Lorem ipsum dolor sit amet, consectetur adipiscing elit.</p>
      <p class="plan-row">Sed ut perspiciatis unde omnis iste natus error</p>
      <p class="plan-row">At vero eos et accusamus et iusto odio dignissimos ducimus.</p>
    </div>
    <div class="btn" style="left:107px;top:384px;width:90px;height:29px;font-size:11px">Register</div>
  </div>
</section>

<!-- News -->
<section class="abs news">
  <h2 class="heading section-title" style="top:44px">LATEST NEWS</h2>
  <div class="title-rule" style="top:91px"></div>

  <article class="news-card" style="left:131px">
    <div class="news-photo" role="img" aria-label="Photo of a person typing on a laptop at a desk" style="background:linear-gradient(120deg,#2f3338,#6f7880 55%,#c9cfd4)"></div>
    <h3 class="news-title">Sed ut perspiciatis unde omnis iste natus error</h3>
    <p class="news-text">At vero eos et accusamus et iusto odio dignissimos ducimus qui blanditiis praese ntium voluptatum deleniti.</p>
    <div class="btn btn-offset" style="left:24px;top:308px;width:82px;height:24px;font-size:8.5px">Read More</div>
  </article>

  <article class="news-card" style="left:450px">
    <div class="news-photo" role="img" aria-label="Photo of hands on a laptop showing a bar chart" style="background:linear-gradient(120deg,#a88b6a,#d9cdbf 50%,#eef0f4)"></div>
    <h3 class="news-title">Sed ut perspiciatis unde omnis iste natus error</h3>
    <p class="news-text">At vero eos et accusamus et iusto odio dignissimos ducimus qui blanditiis praese ntium voluptatum deleniti.</p>
    <div class="btn btn-offset" style="left:24px;top:308px;width:82px;height:24px;font-size:8.5px">Read More</div>
  </article>

  <article class="news-card" style="left:768px">
    <div class="news-photo" role="img" aria-label="Photo of a tennis player hitting a ball at sunset" style="background:linear-gradient(120deg,#8a5a3a,#d9904f 50%,#e9c9a0)"></div>
    <h3 class="news-title">Sed ut perspiciatis unde omnis iste natus error</h3>
    <p class="news-text">At vero eos et accusamus et iusto odio dignissimos ducimus qui blanditiis praese ntium voluptatum deleniti.</p>
    <div class="btn btn-offset" style="left:24px;top:308px;width:82px;height:24px;font-size:8.5px">Read More</div>
  </article>
</section>

<!-- Benefits -->
<section>
  <div class="abs benefit-photo" role="img" aria-label="Close-up photo of a tennis racket striking a ball on a clay court"></div>

  <div class="benefit" style="top:3024px">
    <svg class="benefit-icon" width="58" height="58" viewBox="0 0 58 58" fill="none" stroke="#5500ff" stroke-width="2.5"><rect x="6" y="6" width="26" height="16" rx="3"/><path d="M11 12h16M11 17h10M14 22l-3 5 7-5"/><path d="M26 36c2-4 6-4 7-2l2 4c1 2-1 3-2 4 2 5 5 8 9 9 1-1 2-3 4-2l4 2c2 1 2 5-2 7-8 2-22-12-22-22z"/></svg>
    <h3 class="benefit-title">GREAT SUPPORT</h3>
    <p class="benefit-text">At vero eos et accusamus et iusto odio dignissimos ducimus qui blanditiis praese ntium voluptatum deleniti excepturi sint occaecati cupiditate non provi.</p>
  </div>

  <div class="benefit" style="top:3215px">
    <svg class="benefit-icon" width="58" height="58" viewBox="0 0 58 58" fill="none" stroke="#5500ff" stroke-width="3"><path d="M30 14H10v34h34V28"/><path d="M44 8l6 6-20 20-8 2 2-8z"/></svg>
    <h3 class="benefit-title">SIMPLE TO USE</h3>
    <p class="benefit-text">At vero eos et accusamus et iusto odio dignissimos ducimus qui blanditiis praese ntium voluptatum deleniti excepturi sint occaecati cupiditate non provi.</p>
  </div>

  <div class="benefit" style="top:3400px">
    <svg class="benefit-icon" width="58" height="58" viewBox="0 0 58 58" fill="none" stroke="#5500ff" stroke-width="2.5"><rect x="8" y="12" width="30" height="22" rx="1"/><path d="M4 38h32"/><rect x="38" y="22" width="14" height="26" rx="2"/><path d="M43 44h4"/></svg>
    <h3 class="benefit-title">FULLY RESPONSIVE</h3>
    <p class="benefit-text">At vero eos et accusamus et iusto odio dignissimos ducimus qui blanditiis praese ntium voluptatum deleniti excepturi sint occaecati cupiditate non provi.</p>
  </div>
</section>

<!-- Call to action -->
<section class="abs cta">
  <div class="abs cta-photo" role="img" aria-label="Photo of two colleagues in suits working together at a laptop"></div>
  <h2 class="abs cta-title">At vero eos et accusamus et iusto odio dignissimos</h2>
  <p class="abs cta-text">On the other hand, we denounce with righteous indignation and dislike men who are so beguiled and demoralized by the charms of pleasure of the moment, so blinded by desire</p>
  <div class="btn btn-offset" style="left:655px;top:270px;width:122px;height:40px;font-size:13px">Contact Us</div>
</section>

<!-- Footer -->
<footer class="abs footer">
  <div class="abs logo" style="left:131px;top:103px;font-size:24px"><span class="logo-mark" style="width:26px;height:26px"></span>Zeitfeldo</div>

  <div class="footer-head" style="left:498px">MENU</div>
  <ul class="footer-menu">
    <li>Home</li><li>About Us</li><li>Features</li><li>Pricing</li><li>Contact Us</li>
  </ul>

  <div class="footer-head" style="left:702px">CONTACT US</div>
  <div class="footer-item" style="left:702px;top:82px"><span class="footer-dot"><svg width="10" height="12" viewBox="0 0 10 12"><path d="M5 0a4 4 0 014 4c0 3-4 8-4 8S1 7 1 4a4 4 0 014-4z" fill="#1f1f1f"/><circle cx="5" cy="4" r="1.5" fill="#fff"/></svg></span><span>2150 Harbor Lane<br>Brookfield, CA 90210</span></div>
  <div class="footer-item" style="left:702px;top:133px"><span class="footer-dot"><svg width="11" height="11" viewBox="0 0 11 11"><path d="M2 1l2 0 1 3-1 1c1 2 2 3 4 4l1-1 3 1v2c-5 1-11-5-10-10z" fill="#1f1f1f"/></svg></span><span>Call Us<br>555.014.2276</span></div>
  <div class="footer-item" style="left:702px;top:184px"><span class="footer-dot"><svg width="11" height="9" viewBox="0 0 11 9"><rect x="0" y="0" width="11" height="9" fill="#1f1f1f"/><path d="M0 0l5.5 5L11 0" stroke="#fff" fill="none"/></svg></span><span>E mail Us<br>info@zeitfeldo.com</span></div>

  <div class="footer-head" style="left:966px">FOLLOW US</div>
  <div class="footer-item" style="left:966px;top:82px"><span class="footer-dot"></span><span>Like us on<br>PAGEFEED</span></div>
  <div class="footer-item" style="left:966px;top:133px"><span class="footer-dot"></span><span>Follow us on<br>CHIRPLINE</span></div>
  <div class="footer-item" style="left:966px;top:184px"><span class="footer-dot"></span><span>Follow us on<br>WORKLINK</span></div>

  <div class="footer-rule"></div>
  <p class="copyright">Copyright © 2021 All Rights Reserved</p>
</footer>

</body>
</html>
```